We need a new business card that reflects who we are. Professional, classy, modern, and service ori

We need a business card design for a window coverings design company in Kansas City called Bright Lane Interiors. We offer professional, modern, and high quality window covering products. We are looking to portray an image of a big, national franchise. We are a 5 location (with showrooms) business with 10 professional designers and 4 professional installers. These cards will be used with Thank you cards, given to realtors, and asked for referrals with.

Target Market(s)

Kansas City

Industry/Entity Type

Business

Contact Information for Business Card

We would like our card to look clean and simple on the front, featuring our logo and Marlow Fenwick's. Our designers' phone numbers and emails should be displayed as well as their title.

Font styles to use
Sans Serif

Colors

Designer to choose colors to be used in the design.

Requirements
Must have
• Front - Logos, name, phone number, email address
• Back - Showroom locations, social media? Appt date/time?
Nice to have
• I would like a clean and modern look (not contemporary. I like a white background, but I am open to ideas. Looking for a "National chain" look for a small business.
Should not have
• Too much busyness.

```html
<!DOCTYPE html>
<html lang="en">
<head>
<meta charset="utf-8">
<title>Bright Lane Interiors – Business Card</title>
<link rel="stylesheet" href="https://fonts.googleapis.com/css2?family=Roboto:wght@400;500;700&family=Roboto+Condensed:wght@400;500;700&display=swap">
<style>
  :root {
    --page-bg: #2a2a2a;
    --card-bg: #f4f4f4;
    --brand-red: #c9393e;
    --ink: #1a1a1a;
    --text-grey: #4d4d4d;
    --soft-grey: #8a8a8a;
    --rule: #8c8c8c;
    --accent-orange: #e8892f;
  }
  * { margin: 0; padding: 0; box-sizing: border-box; }
  html, body {
    width: 1200px; height: 960px; overflow: hidden;
    background: var(--page-bg);
    font-family: "Roboto", Arial, sans-serif;
  }
  .canvas { position: relative; width: 1200px; height: 960px; }

  .card {
    position: absolute;
    width: 600px; height: 342px;
    background: var(--card-bg);
  }
  .card--front { left: 322px; top: 108px; }
  .card--back  { left: 320px; top: 493px; }

  /* brand lockup */
  .brand { position: absolute; width: 270px; text-align: center; }
  .brand__mark {
    display: flex; align-items: center; justify-content: center; gap: 8px;
  }
  .brand__square { flex: 0 0 18px; width: 18px; height: 18px; background: var(--brand-red); }
  .brand__name {
    font-weight: 500; font-size: 22px; line-height: 26px; color: var(--ink);
    white-space: nowrap;
  }
  .brand__tagline {
    margin-top: 6px; font-size: 11px; color: var(--ink); white-space: nowrap;
  }
  .card--front .brand { left: 321px; top: 122px; }
  .card--back .brand  { left: 49px;  top: 127px; }

  /* front details */
  .person { position: absolute; left: 28px; top: 198px; }
  .person__name {
    font-family: "Roboto Condensed", Arial, sans-serif;
    font-weight: 500; font-size: 25px; color: var(--brand-red); line-height: 1;
  }
  .person__title {
    margin-top: 5px; font-weight: 500; font-size: 14.5px;
    color: var(--ink); letter-spacing: 0.3px;
  }
  .divider {
    position: absolute; left: 28px; top: 250px; width: 530px; height: 1px;
    background: var(--rule);
  }
  .contact { position: absolute; left: 28px; top: 262px; list-style: none; }
  .contact__item {
    display: flex; align-items: center; gap: 8px;
    font-size: 14px; color: var(--text-grey); line-height: 20px;
  }
  .contact__icon { width: 13px; height: 13px; fill: var(--brand-red); }
  .website {
    position: absolute; right: 27px; top: 282px;
    font-size: 14.5px; color: var(--text-grey);
  }
  .card__band {
    position: absolute; left: 0; bottom: 0; width: 100%; height: 19px;
    border-top: 3px solid #222; background: var(--brand-red);
  }

  /* back details */
  .showrooms { position: absolute; left: 340px; top: 40px; }
  .showrooms__heading {
    font-weight: 700; font-size: 14px; color: var(--brand-red); letter-spacing: 0.2px;
  }
  .showrooms__list { list-style: none; margin-top: 1px; }
  .showrooms__list li {
    font-weight: 500; font-size: 14px; color: var(--text-grey);
    line-height: 18px; letter-spacing: 0.4px;
  }
  .partner {
    position: absolute; left: 340px; top: 154px;
    display: flex; align-items: center; gap: 5px;
    font-size: 12px; font-weight: 500; color: var(--soft-grey);
  }
  .partner__dot { width: 16px; height: 16px; border-radius: 50%; background: var(--accent-orange); }
  .social { position: absolute; left: 339px; top: 183px; display: flex; gap: 3px; }
  .social__dot { width: 17px; height: 17px; border-radius: 50%; background: var(--brand-red); }

  .appointment { position: absolute; left: 43px; color: var(--brand-red); font-size: 16px; }
  .appointment--name { top: 234px; width: 496px; }
  .appointment--when { top: 275px; width: 500px; }
  .appointment__row { display: flex; align-items: baseline; }
  .appointment__fill {
    flex: 1; border-bottom: 1px dotted #555; margin: 0 4px; height: 12px;
  }
  .appointment__fill--date { flex: 0 0 212px; }
  .appointment__suffix { font-size: 12px; }
</style>
</head>
<body>
<main class="canvas">

  <section class="card card--front" aria-label="Business card front">
    <div class="brand">
      <div class="brand__mark">
        <span class="brand__square"></span>
        <span class="brand__name">Bright Lane Interiors</span>
      </div>
      <p class="brand__tagline">Blinds, Shades, Shutters, Draperies &amp; Decor</p>
    </div>

    <div class="person">
      <p class="person__name">EVAN MARSH</p>
      <p class="person__title">DESIGNER</p>
    </div>
    <div class="divider"></div>

    <ul class="contact">
      <li class="contact__item">
        <svg class="contact__icon" viewBox="0 0 24 24" aria-hidden="true"><path d="M6.6 10.8a15.1 15.1 0 0 0 6.6 6.6l2.2-2.2c.3-.3.7-.4 1-.2 1.1.4 2.3.6 3.6.6.6 0 1 .4 1 1V20c0 .6-.4 1-1 1A17 17 0 0 1 3 4c0-.6.4-1 1-1h3.5c.6 0 1 .4 1 1 0 1.3.2 2.5.6 3.6.1.3 0 .7-.2 1z"/></svg>
        913.555.0148
      </li>
      <li class="contact__item">
        <svg class="contact__icon" viewBox="0 0 24 24" aria-hidden="true"><rect x="2" y="5" width="20" height="14" rx="1"/><path d="M3 6.5l9 6.5 9-6.5" fill="none" stroke="#f4f4f4" stroke-width="1.8"/></svg>
        info@brightlaneinteriors.com
      </li>
    </ul>
    <p class="website">www.brightlaneinteriors.com</p>
    <div class="card__band"></div>
  </section>

  <section class="card card--back" aria-label="Business card back">
    <div class="brand">
      <div class="brand__mark">
        <span class="brand__square"></span>
        <span class="brand__name">Bright Lane Interiors</span>
      </div>
      <p class="brand__tagline">Blinds, Shades, Shutters, Draperies &amp; Decor</p>
    </div>

    <div class="showrooms">
      <p class="showrooms__heading">SHOWROOM LOCATIONS</p>
      <ul class="showrooms__list">
        <li>MAPLE RIDGE</li>
        <li>CEDAR HOLLOW</li>
        <li>PINE CREST</li>
        <li>WILLOW BEND</li>
        <li>OAK HAVEN</li>
      </ul>
    </div>
    <div class="partner">
      <span>Marlow Fenwick Gallery</span>
      <span class="partner__dot"></span>
    </div>
    <div class="social" aria-label="Social media">
      <span class="social__dot"></span><span class="social__dot"></span>
      <span class="social__dot"></span><span class="social__dot"></span>
    </div>

    <div class="appointment appointment--name appointment__row">
      <span>Name :</span><span class="appointment__fill"></span>
    </div>
    <div class="appointment appointment--when appointment__row">
      <span>Date :</span><span class="appointment__fill appointment__fill--date"></span>
      <span>Time :</span><span class="appointment__fill"></span>
      <span class="appointment__suffix">AM/PM</span>
    </div>
  </section>

</main>
</body>
</html>
```